The Harbourlight Dental centre, the Zorvik of dentistry

New concept of running a dental practice by having a walk in practice
WE ARE A HUSBAND AND WIFE TEAM

Really modern and sophisticated, we want it to feel different from the traditional dental practice.
we want it split into different pages:CONTACT US
LOCATION: Information about our location since patients often confuse us with the practice across the road
ABOUT US:
Opening hours - & 7 Days, We offer a weekend service
WALK IN: We offer a walk in service for dental treatments
TREATMENTS we offer

DENTAL ADVICE: Free dentist advise call back- So a dentist will call you back for free to discuss

Target Market(s)

Everyone

Industry/Entity Type

Dental

Coding

Coded - Design and coding required

Number of Pages Required

5+ page

Requirements
Must have
• First page
• * changing pictures
• *opening times
• * our walk in concept I.e. no appointment needed
• *logo
• * links in to clinic tidal (online booking system in Australia)
• * address /phone number/email
• * possible videos
• Second page
• meet the team
• third page
• dental treatments/walk in treatments
• fourth page
• dental advice with vid larko videos
• Fifth page
• contact us/maps/ we get confused with the dental practice across the road
• We would also like a giving back page. In this please include the photo's below of our dental mission in Guatemala, where by we did treatment for patients as part of a charity.
Nice to have
• Changing pictures on the home screen
• videos linked to home page

```html
<!DOCTYPE html>
<html lang="en">
<head>
<meta charset="utf-8">
<title>The Harbourlight Dental centre</title>
<link href="https://fonts.googleapis.com/css2?family=Open+Sans:wght@300;400;600;700&display=swap" rel="stylesheet">
<style>
:root{
  --green:#9dc43c;
  --blue:#0eb0ea;
  --ink:#444;
  --muted:#777;
  --pale:#f3f3f3;
  --footer:#3b3b3b;
  --dark:#333;
}
*{box-sizing:border-box;margin:0;padding:0}
html,body{width:687px;height:1200px;overflow:hidden;background:#fff}
body{position:relative;font-family:'Open Sans',Arial,sans-serif;color:var(--ink)}
.abs{position:absolute}
.top-stripe{left:0;top:0;width:687px;height:3px;background:linear-gradient(90deg,var(--green) 55%,var(--blue) 100%)}
.brand{left:76px;top:14px;display:flex;align-items:center;gap:8px}
.brand-mark{width:34px;height:34px;border-radius:50%;background:var(--blue)}
.brand-name{font-size:14px;font-weight:700;color:var(--green);line-height:1}
.brand-sub{font-size:6px;letter-spacing:1.5px;color:var(--green);margin-top:3px;text-transform:uppercase}
.top-info{right:76px;top:27px;text-align:right;font-size:5.6px;color:var(--muted)}
.top-info span{margin-left:8px}
.top-contact{right:76px;top:38px;font-size:9px;color:var(--blue);display:flex;gap:10px;align-items:center}
.top-contact svg{vertical-align:-1px;margin-right:3px}
.main-nav{left:76px;top:72px;width:535px;height:30px;background:var(--green);display:flex;align-items:center}
.main-nav a{font-size:7px;color:#fff;text-decoration:none;text-transform:uppercase;height:30px;line-height:30px;padding:0 0 0 0}
.main-nav .active{background:var(--blue);width:52px;text-align:center}
.nav-item{flex:1;text-align:center}
.hero{left:0;top:102px;width:687px;height:208px;background:linear-gradient(180deg,#dfe6ee 0%,#eeeeee 45%,#9a9a95 100%)}
.hero-arrow{top:195px;color:#fff;font-size:10px}
.banner-left{left:0;top:310px;width:343px;height:41px;background:var(--blue);color:#fff;font-size:7.4px;font-weight:700;padding:10px 0 0 76px;line-height:1.45;text-transform:uppercase}
.banner-right{left:343px;top:310px;width:344px;height:41px;background:var(--green);color:#fff;font-size:12px;font-weight:700;text-align:center;line-height:41px}
.video-thumb{left:76px;top:381px;width:139px;height:110px;background:linear-gradient(135deg,#4a5a80,#8c8a88 60%,#c9b9a8)}
.play{left:136px;top:427px;width:20px;height:20px;border-radius:50%;background:var(--blue);border:2px solid #fff}
.play::after{content:"";position:absolute;left:6px;top:4px;border-left:7px solid #fff;border-top:4px solid transparent;border-bottom:4px solid transparent}
.welcome-title{left:227px;top:376px;font-size:19px;font-weight:400;color:var(--green)}
.welcome-text{left:227px;top:405px;width:385px;font-size:6.3px;line-height:1.75;color:#555}
.welcome-box{left:227px;top:444px;width:384px;height:48px;border:1px solid var(--blue);padding:10px 16px;color:var(--blue);font-size:9px;line-height:1.4}
.welcome-box strong{font-weight:400;font-size:11px;text-transform:uppercase}
.services{left:0;top:525px;width:687px;height:316px;background:var(--pale)}
.section-title{width:687px;text-align:center;font-size:19px;color:var(--green);font-weight:400}
.card{width:126px;height:110px}
.card-photo{width:126px;height:87px}
.card-label{height:23px;background:var(--blue);color:#fff;font-size:8.6px;font-weight:600;padding:5px 8px}
.testimonials-title{left:0;top:862px;width:687px;text-align:center;font-size:23px;font-weight:700;color:#d6d6d6;text-transform:uppercase}
.quote{left:0;top:898px;width:687px;text-align:center;font-size:12px;color:#333}
.quote b{color:#bbb;font-size:16px;font-weight:700;font-style:italic}
.quote-name{left:0;top:922px;width:687px;text-align:center;font-size:9px;color:#333}
.dots{left:318px;top:946px;display:flex;gap:9px}
.dots i{width:5px;height:5px;border-radius:50%;background:#ccc;display:block}
.dots i:first-child{background:var(--green)}
.map{left:0;top:975px;width:343px;height:142px;background:linear-gradient(135deg,#d9d9d9,#c4c4c4 50%,#d6d6d6)}
.contact{left:343px;top:975px;width:344px;height:142px;background:#efefef}
.contact h2{position:absolute;left:29px;top:16px;font-size:14px;font-weight:400;color:#333}
.field{width:104px;height:20px;background:#fff;font-size:6.4px;color:#888;padding:6px 10px}
.submit{background:var(--dark);color:#fff;text-align:center;font-size:6.6px;padding:6px 0;text-transform:uppercase}
.footer{left:0;top:1117px;width:687px;height:83px;background:var(--footer);color:#ddd}
.foot-row{position:absolute;top:14px;font-size:6.4px;display:flex;align-items:center;gap:4px}
.foot-line{position:absolute;left:76px;top:34px;width:535px;height:1px;background:#555}
.foot-links{position:absolute;left:76px;top:47px;font-size:5.4px;color:#ccc}
.foot-copy{position:absolute;left:76px;top:62px;font-size:5.4px;color:#ccc}
.social{position:absolute;right:76px;top:13px;display:flex;gap:10px}
.social i{width:6px;height:6px;background:#888;display:block}
.booking{position:absolute;right:76px;top:51px;display:flex;align-items:center;gap:10px;font-size:5.4px;color:#ccc}
.booking-name{font-size:12px;color:#aaa;font-weight:400;display:flex;align-items:center;gap:4px}
.booking-name i{width:10px;height:10px;background:#aaa;display:block}
</style>
</head>
<body>
<div class="abs top-stripe"></div>

<header>
  <div class="abs brand">
    <div class="brand-mark"></div>
    <div>
      <div class="brand-name">The Harbourlight</div>
      <div class="brand-sub">Dental centre</div>
    </div>
  </div>
  <div class="abs top-info">
    <span>&#9679; Unit 7, 18 Kestrel Parade, Brightwater, WA 6099.</span>
    <span>&#9675; OPEN 8 AM TO 8PM 7 DAYS A WEEK</span>
  </div>
  <div class="abs top-contact">
    <span><svg width="8" height="8" viewBox="0 0 10 10"><path d="M2 1l2 2-1 1.5c.6 1.2 1.4 2 2.5 2.5L7 6l2 2-1 1.5C4.5 9 1 5.5.5 2z" fill="#0eb0ea"/></svg>08 5550 2718</span>
    <span><svg width="9" height="7" viewBox="0 0 10 8"><rect width="10" height="8" fill="#0eb0ea"/><path d="M0 0l5 4 5-4" stroke="#fff" fill="none"/></svg>hello@harbourlightdental.example</span>
  </div>
  <nav class="abs main-nav">
    <a class="active" href="#">Home</a>
    <a class="nav-item" href="#">About Us</a>
    <a class="nav-item" href="#">Services</a>
    <a class="nav-item" href="#">Treatments</a>
    <a class="nav-item" href="#">Dentists</a>
    <a class="nav-item" href="#">Location</a>
    <a class="nav-item" href="#">Blog</a>
    <a class="nav-item" href="#">Contact Us</a>
  </nav>
</header>

<section>
  <div class="abs hero" role="img" aria-label="Photo of the clinic's white shopfront in a medical centre with cars parked outside"></div>
  <div class="abs hero-arrow" style="left:6px">&#8592;</div>
  <div class="abs hero-arrow" style="right:6px">&#8594;</div>
  <div class="abs banner-left">We understand that everyone has a busy life and we<br>want dental treatment to be accessible for all.</div>
  <div class="abs banner-right">No Appointment Needed!</div>
</section>

<section>
  <div class="abs video-thumb" role="img" aria-label="Video still of a dentist treating a patient"></div>
  <div class="abs play"></div>
  <h1 class="abs welcome-title">Welcome to The Harbourlight Dental Centre</h1>
  <p class="abs welcome-text">Your general and cosmetic dentist in the heart of vibrant Brightwater. Whether it's cosmetic hygiene treatment, tooth whitening, or botox facial rejuvenation.<br>Located within the busy medical centre with free parking all around.</p>
  <div class="abs welcome-box">Please call or pop in and one of our helpful team will be only too happy to help for<br><strong>All your dental needs.</strong></div>
</section>

<section class="abs services">
  <h2 class="abs section-title" style="top:32px">Our Services</h2>
  <div class="abs card" style="left:76px;top:54px"><div class="card-photo" role="img" aria-label="Dentist performing an extraction" style="background:linear-gradient(135deg,#3c4f80,#7a8aa8)"></div><div class="card-label">Extractions</div></div>
  <div class="abs card" style="left:212px;top:54px"><div class="card-photo" role="img" aria-label="Team fitting dentures" style="background:linear-gradient(135deg,#cfcfcf,#4e5f8c)"></div><div class="card-label">Dentures</div></div>
  <div class="abs card" style="left:348px;top:54px"><div class="card-photo" role="img" aria-label="Outdoor clinic doing fillings" style="background:linear-gradient(135deg,#bdbdbd,#5a5a5a)"></div><div class="card-label">Fillings</div></div>
  <div class="abs card" style="left:484px;top:54px"><div class="card-photo" role="img" aria-label="Patients waiting at a community clinic" style="background:linear-gradient(135deg,#e2e2dc,#5e5e5e)"></div><div class="card-label">Root Canal Treatment</div></div>
  <div class="abs card" style="left:76px;top:174px"><div class="card-photo" role="img" aria-label="Treatment room with green dental chair" style="background:linear-gradient(135deg,#f0f0f0,#9ac46a)"></div><div class="card-label">Periodontal Treatment</div></div>
  <div class="abs card" style="left:212px;top:174px"><div class="card-photo" role="img" aria-label="Dentist fitting a crown" style="background:linear-gradient(135deg,#4a5a80,#c9b9a8)"></div><div class="card-label">Crowns and Bridges</div></div>
  <div class="abs card" style="left:348px;top:174px"><div class="card-photo" role="img" aria-label="Teeth whitening treatment" style="background:linear-gradient(135deg,#3c4f80,#8a8a8a)"></div><div class="card-label">Teeth Whitening</div></div>
  <div class="abs card" style="left:484px;top:174px"><div class="card-photo" role="img" aria-label="Smiling clinic team members" style="background:linear-gradient(135deg,#e8e8e8,#3a3a4a)"></div><div class="card-label">Facial Aesthetics</div></div>
</section>

<section>
  <h2 class="abs testimonials-title">Testimonials</h2>
  <p class="abs quote"><b>&ldquo;</b> Etiam quis magna nec odio sagittis pretium id eget risus eget fermentum magna arcu. <b>&rdquo;</b></p>
  <p class="abs quote-name">Mark Fenwick, City</p>
  <div class="abs dots"><i></i><i></i><i></i><i></i></div>
</section>

<section>
  <div class="abs map" role="img" aria-label="Grey world map"></div>
  <form class="abs contact">
    <h2>Contact Us</h2>
    <div class="abs field" style="left:29px;top:40px">First Name</div>
    <div class="abs field" style="left:139px;top:40px">Last Name</div>
    <div class="abs field" style="left:29px;top:67px">Phone</div>
    <div class="abs field" style="left:139px;top:67px">Email</div>
    <div class="abs field" style="left:29px;top:95px">City</div>
    <div class="abs field submit" style="left:139px;top:95px">Submit</div>
  </form>
</section>

<footer class="abs footer">
  <div class="foot-row" style="left:76px"><svg width="6" height="8" viewBox="0 0 6 8"><path d="M3 0a3 3 0 013 3c0 2-3 5-3 5S0 5 0 3a3 3 0 013-3z" fill="#ddd"/></svg> Unit 7, 18 Kestrel Parade, Brightwater, WA 6099</div>
  <div class="foot-row" style="left:279px"><svg width="7" height="7" viewBox="0 0 10 10"><path d="M2 1l2 2-1 1.5c.6 1.2 1.4 2 2.5 2.5L7 6l2 2-1 1.5C4.5 9 1 5.5.5 2z" fill="#ddd"/></svg> Call Now: 08 5550 2718</div>
  <div class="foot-row" style="left:387px"><svg width="9" height="7" viewBox="0 0 10 8"><rect width="10" height="8" fill="#ddd"/><path d="M0 0l5 4 5-4" stroke="#3b3b3b" fill="none"/></svg> Email: hello@harbourlightdental.example</div>
  <div class="social"><i></i><i></i><i></i><i></i></div>
  <div class="foot-line"></div>
  <div class="foot-links">Home &nbsp;|&nbsp; Meet the Team &nbsp;|&nbsp; Dental Treatments/Walk-in Treatments &nbsp;|&nbsp; Dental Advice &nbsp;|&nbsp; Contact us</div>
  <div class="foot-copy">Copyright &copy; 2016 The Harbourlight Dental centre. &nbsp;All rights reserved.</div>
  <div class="booking">Appointment Booking <span class="booking-name"><i></i>clinic tidal</span></div>
</footer>
</body>
</html>
```